Business Card - high end, modern health care

Hey designers!

We need a double sided business card for the boutique, cutting edge physical therapy rehabilitation centre in Sydney's Northern Beaches.

With the most qualified physios in the area The Harbourview Motion Clinic does what other physiotherapy practices do not, we take our time with our patients giving them longer appointments, better physios and therefor faster results!

We guarantee that the service people receive at THMC will be unparalleled.

Hence we need a business card to reflect our modern, boutique, high end service. The final design needs to reflect that we are in a class of our own yet with the feel of beachside retreat.

Below I have attached our logo in both blue on white and white on blue. The exact colour is;
and the font that we have used in our logo is Tex Gyre Aventador.

I like the idea of the blue as the main colour as it is more eye catching and our signage onto the main road will be in this blue and in the interest of consistency across marketing the blue needs to be a part of the design. However I would appreciate a few designs onto a wooden background as this is a visual theme within the fitout of the practice.

The design needs to be of standard size (91x55mm).

Target Market(s)

We target people who have an end outcome in mind and those who have had poor experiences with other providers and ensure that everyone gets the care that they deserve with a premium service that is tailored to the individuals circumstances. As a premium service, the target market is highly educated, business and tech savvy with the additional target market of elderly people who have self funded their retirement and see value in paying for the best ongoing rehabilitation to maintain independence.

Industry/Entity Type

Physical Therapy

Contact Information for Business Card

Name, designation( Titled Musculoskeletal Physiotherapist... there will also be those in the company that have multiple designations ie 5 or 6 words long), phone number, email, facebook, instagram, address

Font styles to use
Sans Serif

Colors

Designer to choose colors to be used in the design.

Requirements
Must have
• Front - The logo as large as possible, blue or wooden theme, and all of the important details.
• Back - A blank space/lines on which to write appointment times (no "Appointment, date, time" etc.)
Nice to have
• facebook url
• logos for facebook and instagram
• Mini logos for the phone and email?

```html
<!DOCTYPE html>
<html lang="en">
<head>
<meta charset="utf-8">
<title>The Harbourview Motion Clinic – Business Card</title>
<link href="https://fonts.googleapis.com/css2?family=Roboto:wght@400;700&family=Roboto+Condensed:wght@700&display=swap" rel="stylesheet">
<style>
  :root {
    --brand-blue: #1d58a8;
    --brand-blue-dark: #174a90;
    --ink: #55585c;
    --rule: #8a8d91;
    --paper: #ffffff;
    --tint: #e6ebf2;
    --backdrop: #ecebe8;
  }
  * { box-sizing: border-box; margin: 0; padding: 0; }
  html, body { width: 1200px; height: 911px; overflow: hidden; }
  body {
    background: var(--backdrop);
    font-family: "Roboto", Arial, sans-serif;
    position: relative;
  }
  .card {
    position: absolute;
    top: 298px;
    width: 520px;
    height: 314px;
    background: var(--paper);
    border-radius: 20px;
    overflow: hidden;
    box-shadow: 0 6px 18px rgba(0,0,0,.12);
  }
  .card--front { left: 60px; }
  .card--back { left: 620px; }

  .watermark {
    position: absolute;
    border-radius: 50%;
    background: var(--tint);
    opacity: .75;
  }
  .card--front .watermark { width: 250px; height: 250px; right: 20px; top: -70px; }
  .card--back .watermark { width: 230px; height: 230px; left: 150px; top: 110px; }

  .contact-strip {
    position: absolute;
    left: 34px; top: 112px; bottom: 0;
    width: 38px;
    background: var(--brand-blue);
  }
  .contact-strip svg { display: block; margin: 0 auto; }
  .contact-strip .icon { margin-top: 12px; }

  .brand {
    position: absolute;
    left: 28px; top: 60px;
    display: flex; align-items: center; gap: 10px;
  }
  .brand__dot {
    width: 50px; height: 50px;
    border-radius: 50%;
    background: var(--brand-blue);
    flex: none;
  }
  .brand__name {
    font-weight: 700;
    color: var(--brand-blue);
    font-size: 22px;
    line-height: 1.02;
    letter-spacing: .01em;
    text-transform: uppercase;
  }

  .contact-list {
    position: absolute;
    left: 92px; top: 140px;
    list-style: none;
    color: var(--ink);
    font-size: 12.5px;
    line-height: 16px;
  }
  .contact-list li.gap { margin-top: 10px; }

  .person {
    position: absolute;
    right: 42px; top: 130px;
    text-align: right;
  }
  .person__name {
    font-family: "Roboto Condensed", "Arial Narrow", sans-serif;
    font-weight: 700;
    font-size: 24px;
    color: var(--brand-blue);
    line-height: 1;
  }
  .person__title {
    font-size: 12.5px;
    color: var(--ink);
    margin-top: 3px;
  }

  .appointments {
    position: absolute;
    left: 34px; right: 34px; top: 30px;
    color: var(--ink);
    font-size: 13px;
  }
  .appt-line {
    display: flex; align-items: flex-end; gap: 6px;
    height: 32px;
  }
  .appt-line .fill { flex: 1; border-bottom: 1px solid var(--rule); height: 1px; margin-bottom: 4px; }
  .appt-line .fill--short { flex: .55; }
  .appt-line.blank { border-bottom: 1px solid var(--rule); }
</style>
</head>
<body>

<section class="card card--front" aria-label="Business card front">
  <div class="watermark" role="img" aria-label="Faint brand circle"></div>

  <div class="contact-strip">
    <svg class="icon" width="14" height="16" viewBox="0 0 14 16" aria-label="Address"><path d="M7 1a5 5 0 0 0-5 5c0 4 5 9 5 9s5-5 5-9a5 5 0 0 0-5-5z" fill="#fff"/><circle cx="7" cy="6" r="2" fill="var(--brand-blue)"/></svg>
    <svg class="icon" width="14" height="14" viewBox="0 0 14 14" aria-label="Phone" style="margin-top:40px"><path d="M3 1l2 3-1.3 1.3a8 8 0 0 0 5 5L10 9l3 2-1 2c-6 0-11-5-11-11z" fill="#fff"/></svg>
    <svg class="icon" width="14" height="11" viewBox="0 0 14 11" aria-label="Email"><rect x=".5" y=".5" width="13" height="10" rx="1" fill="#fff"/><path d="M1 1l6 5 6-5" stroke="var(--brand-blue)" fill="none"/></svg>
    <svg class="icon" width="14" height="14" viewBox="0 0 14 14" aria-label="Website"><circle cx="7" cy="7" r="6" fill="none" stroke="#fff" stroke-width="1.5"/><path d="M1 7h12M7 1c-3 3-3 9 0 12M7 1c3 3 3 9 0 12" stroke="#fff" fill="none"/></svg>
    <svg class="icon" width="13" height="13" viewBox="0 0 13 13" aria-label="Social page"><rect width="13" height="13" rx="2" fill="#fff"/></svg>
    <svg class="icon" width="13" height="13" viewBox="0 0 13 13" aria-label="Social handle"><rect x=".75" y=".75" width="11.5" height="11.5" rx="3" fill="none" stroke="#fff" stroke-width="1.5"/></svg>
  </div>

  <div class="brand">
    <span class="brand__dot"></span>
    <span class="brand__name">The Harbourview<br>Motion Clinic</span>
  </div>

  <ul class="contact-list">
    <li>42 Tidewater Lane</li>
    <li>Dee Why, NSW 2099</li>
    <li class="gap">612 845 3907</li>
    <li>daniel@harbourviewmotion.com</li>
    <li>www.harbourviewmotion.com</li>
    <li>/harbourviewmotion</li>
    <li>@harbourviewmotion</li>
  </ul>

  <div class="person">
    <p class="person__name">DANIEL REYES</p>
    <p class="person__title">CEO/FOUNDER</p>
  </div>
</section>

<section class="card card--back" aria-label="Business card back">
  <div class="watermark" role="img" aria-label="Faint brand circle"></div>
  <div class="appointments">
    <div class="appt-line"><span>Date</span><span class="fill"></span><span>Time</span><span class="fill fill--short"></span><span>am/pm</span></div>
    <div class="appt-line"><span>Date</span><span class="fill"></span><span>Time</span><span class="fill fill--short"></span><span>am/pm</span></div>
    <div class="appt-line blank"></div>
    <div class="appt-line blank"></div>
    <div class="appt-line blank"></div>
    <div class="appt-line blank"></div>
    <div class="appt-line blank"></div>
    <div class="appt-line blank"></div>
  </div>
</section>

</body>
</html>
```